Development of the overall look and feel for the website. www.ReelPalsHub.com

This site is geared as a competitor to some of the major Fan websites. Where we want to be different is making a site geared more towards interaction with the Fans in the Social Media platform.
-Live streaming
-Instant Messaging
-Ability to request and purchase custom digital pieces
-Ability for Models/creators to sell blogs, podcasts, clips, screensavers, etc. through a dedicated online digital store.
-We will also have story like features similar to those found on Photoburst to allow interaction.
-Content Creators keep 85% of earnings

This should be sexy, seductive, bold, and geared towards all spectrums. From Swingers, Kink, Fetish, Milf, College, etc.

Overall the feeling should be Fun with a sense of excitement that is taboo and erotic while not scaring people away.

Trying to find the perfect blend between finding harmony/Norma Whitcombe/GBT/SoloPatron/Velvet Soiree and KRV. Monetization will be most similar to SoloPatron.

Target Market(s)

Target market should be 18+ / All Genders/ All sexuality. I want to be sure to target markets that were traditionally left out from some of the bigger platforms with all lifestyle and gender inclusion.

Industry/Entity Type

Adult Modeling, Adult Website, Streaming, Porn/fetish

Colors

Designer to choose colors to be used in the design.

Requirements
Must have
• Sex Appeal, Curiosity, Call to action, Storyboard to tell what we are about
Nice to have
• uploaded some designs that have overall look/feel.
Should not have
• Sexy but no nudity

```html
<!DOCTYPE html>
<html lang="en">
<head>
<meta charset="utf-8">
<title>ReelPalsHub – Live Session</title>
<link href="https://fonts.googleapis.com/css2?family=Hind:wght@300;400;500;600&display=swap" rel="stylesheet">
<style>
  :root {
    --plum: #7b2872;
    --plum-dark: #6a1f62;
    --plum-soft: #f3e3ee;
    --blush: #fdf1f4;
    --blush-line: #f4dce3;
    --ink: #222026;
    --muted: #9a97a0;
    --line: #e6e4ea;
    --white: #ffffff;
    --rec-red: #e0283a;
    --track: #d9c9d6;
  }
  * { box-sizing: border-box; margin: 0; padding: 0; }
  html, body { width: 1200px; height: 800px; overflow: hidden; }
  body { font-family: "Hind", sans-serif; color: var(--ink); background: var(--white); }
  .app { position: relative; width: 1200px; height: 800px; background: var(--white); }

  /* sidebar */
  .sidebar { position: absolute; left: 0; top: 0; width: 118px; height: 680px; border-right: 1px solid var(--line); }
  .brand { position: absolute; left: 14px; top: 24px; width: 90px; display: flex; flex-direction: column; align-items: center; gap: 4px; }
  .brand-dot { width: 14px; height: 14px; border-radius: 50%; background: var(--plum); }
  .brand-name { font-size: 13px; font-weight: 600; color: var(--plum); }
  .nav { position: absolute; left: 0; top: 132px; width: 118px; display: flex; flex-direction: column; gap: 26px; align-items: center; }
  .nav-item { display: flex; flex-direction: column; align-items: center; gap: 10px; font-size: 12px; color: var(--muted); }
  .nav-icon { width: 46px; height: 46px; border: 1px solid var(--line); border-radius: 8px; display: grid; place-items: center; box-shadow: 0 2px 6px rgba(0,0,0,.04); }
  .nav-icon svg { width: 20px; height: 20px; stroke: #a8a5ae; fill: none; stroke-width: 1.5; }

  /* stage */
  .stage { position: absolute; left: 140px; top: 0; width: 630px; }
  .stage-head { position: absolute; top: 36px; left: 0; width: 630px; height: 48px; border-bottom: 1px solid var(--line); display: flex; align-items: flex-start; gap: 16px; }
  .back-btn { width: 26px; height: 26px; border-radius: 5px; background: #f1f0f3; display: grid; place-items: center; }
  .back-btn svg { width: 10px; height: 10px; stroke: var(--ink); fill: none; stroke-width: 2; }
  .stage-title { font-size: 17px; font-weight: 500; line-height: 26px; }
  .pro-badge { display: inline-flex; align-items: center; gap: 6px; height: 30px; padding: 0 12px; background: var(--plum); color: var(--white); font-size: 15px; font-weight: 600; border-radius: 3px; margin-top: -2px; }
  .pro-badge svg { width: 11px; height: 12px; fill: var(--white); }
  .stage-meta { position: absolute; top: 100px; left: 0; width: 630px; display: flex; justify-content: space-between; align-items: center; font-size: 10px; }
  .record { display: flex; align-items: center; gap: 8px; color: var(--muted); }
  .record-dot { width: 14px; height: 14px; border-radius: 50%; border: 2px solid var(--rec-red); display: grid; place-items: center; }
  .record-dot::after { content: ""; width: 6px; height: 6px; border-radius: 50%; background: var(--rec-red); }
  .invite { display: flex; align-items: center; gap: 7px; color: var(--plum); font-size: 11px; margin-right: 44px; }
  .invite-plus { width: 15px; height: 15px; border-radius: 3px; background: var(--plum); color: var(--white); font-size: 12px; line-height: 16px; text-align: center; }
  .video { position: absolute; top: 128px; left: 0; width: 630px; height: 455px; border-radius: 22px; background: radial-gradient(ellipse at 62% 45%, #3a2a26 0%, #1c1514 45%, #0c0a0a 100%); }
  .stage-foot-line { position: absolute; top: 625px; left: 0; width: 630px; border-top: 1px solid var(--line); }

  /* controls */
  .controls { position: absolute; top: 660px; left: 140px; width: 630px; height: 80px; }
  .volume { position: absolute; left: 0; top: 6px; width: 128px; height: 58px; border: 1px solid var(--line); border-radius: 8px; display: flex; align-items: center; gap: 10px; padding-left: 14px; box-shadow: 0 2px 6px rgba(0,0,0,.04); }
  .volume svg { width: 20px; height: 18px; fill: var(--plum); }
  .volume-track { position: relative; width: 68px; height: 3px; background: var(--track); border-radius: 2px; }
  .volume-track::before { content: ""; position: absolute; left: 0; top: 0; width: 30px; height: 3px; background: var(--plum); border-radius: 2px; }
  .volume-track::after { content: ""; position: absolute; left: 27px; top: -3px; width: 9px; height: 9px; border-radius: 50%; background: var(--white); border: 2px solid var(--plum); }
  .ctrl { position: absolute; top: 0; display: flex; flex-direction: column; align-items: center; gap: 12px; font-size: 12px; color: var(--muted); }
  .ctrl-btn { width: 54px; height: 56px; border: 1px solid var(--line); border-radius: 8px; display: grid; place-items: center; background: var(--white); box-shadow: 0 2px 6px rgba(0,0,0,.04); }
  .ctrl-btn svg { width: 22px; height: 22px; }
  .ctrl-btn.is-active { background: var(--plum); border-color: var(--plum); }
  .ctrl-btn.is-active svg { width: 24px; height: 24px; }

  /* side panel */
  .panel { position: absolute; left: 800px; top: 26px; width: 334px; height: 712px; background: var(--blush); border-radius: 14px; }
  .tabs { position: absolute; top: 30px; left: 24px; width: 286px; height: 66px; background: var(--white); border-radius: 8px; display: flex; align-items: center; padding: 4px; }
  .tab { flex: 1; height: 54px; display: grid; place-items: center; font-size: 17px; color: var(--muted); border-radius: 6px; }
  .tab.is-active { background: var(--plum-soft); color: var(--plum); font-weight: 500; }
  .poll { position: absolute; top: 120px; left: 24px; width: 286px; height: 228px; background: var(--plum); border-radius: 6px; color: var(--white); padding: 22px 20px; overflow: hidden; }
  .poll-q { font-size: 15px; font-weight: 500; line-height: 26px; }
  .poll-q span { display: block; white-space: nowrap; }
  .poll-list { margin-top: 18px; display: flex; flex-direction: column; gap: 14px; }
  .poll-bar { position: relative; height: 3px; background: rgba(255,255,255,.35); border-radius: 2px; margin-bottom: 10px; }
  .poll-bar span { position: absolute; left: 0; top: 0; height: 3px; background: var(--white); border-radius: 2px; }
  .poll-label { font-size: 9.5px; line-height: 12px; }
  .divider { position: absolute; top: 378px; left: 24px; width: 286px; display: flex; align-items: center; gap: 22px; font-size: 15px; color: var(--muted); }
  .divider::before, .divider::after { content: ""; flex: 1; border-top: 1px solid var(--blush-line); }
  .msg { position: absolute; left: 24px; width: 286px; }
  .avatar { position: absolute; left: 0; top: 0; width: 48px; height: 48px; border-radius: 50%; }
  .avatar.devi { background: linear-gradient(160deg, #e9d7c4, #c8a98c); }
  .avatar.octavia { background: linear-gradient(160deg, #a88a6e, #5c4a3e); }
  .msg-name { position: absolute; left: 62px; top: 0; font-size: 15px; color: var(--muted); }
  .bubble { position: absolute; left: 62px; top: 30px; width: 158px; height: 50px; background: var(--white); border-radius: 4px; display: flex; align-items: center; padding-left: 22px; font-size: 11.5px; box-shadow: 0 2px 6px rgba(0,0,0,.03); }
  .you-name { position: absolute; right: 24px; top: 602px; font-size: 15px; color: var(--muted); }
  .bubble-you { position: absolute; right: 24px; top: 632px; width: 142px; height: 48px; background: var(--plum-soft); border-radius: 4px; display: grid; place-items: center; font-size: 11.5px; }
</style>
</head>
<body>
<div class="app">

  <aside class="sidebar">
    <div class="brand">
      <span class="brand-dot"></span>
      <span class="brand-name">ReelPalsHub</span>
    </div>
    <nav class="nav">
      <div class="nav-item"><div class="nav-icon"><svg viewBox="0 0 20 20"><rect x="3" y="3" width="12" height="14" rx="1"/><path d="M6 7h6M6 10h6M6 13h3M12 15l5-7"/></svg></div>Blogs</div>
      <div class="nav-item"><div class="nav-icon"><svg viewBox="0 0 20 20"><rect x="6" y="3" width="6" height="9" rx="3"/><path d="M4 10a5 5 0 0 0 10 0M9 15v3M14 4h3M14 7h3"/></svg></div>Podcasts</div>
      <div class="nav-item"><div class="nav-icon"><svg viewBox="0 0 20 20"><path d="M14 6l-6 6a2 2 0 0 0 3 3l6-6a4 4 0 0 0-6-6l-6 6a6 6 0 0 0 8 8"/></svg></div>Clips</div>
      <div class="nav-item"><div class="nav-icon"><svg viewBox="0 0 20 20"><rect x="3" y="3" width="14" height="10" rx="1"/><path d="M6 6h8M6 9h8M4 16h12M7 13v3M13 13v3"/></svg></div>Screensavers</div>
      <div class="nav-item"><div class="nav-icon"><svg viewBox="0 0 20 20"><rect x="3" y="3" width="5.5" height="5.5" rx="1.5"/><rect x="11.5" y="3" width="5.5" height="5.5" rx="1.5"/><rect x="3" y="11.5" width="5.5" height="5.5" rx="1.5"/><rect x="11.5" y="11.5" width="5.5" height="5.5" rx="1.5"/></svg></div>More</div>
    </nav>
  </aside>

  <main class="stage">
    <header class="stage-head">
      <div class="back-btn"><svg viewBox="0 0 10 10"><path d="M6.5 1.5L3 5l3.5 3.5"/></svg></div>
      <h1 class="stage-title">Lorem ipsum dolor sit amet, consectetur</h1>
      <span class="pro-badge"><svg viewBox="0 0 11 12"><circle cx="5.5" cy="3" r="2.7"/><path d="M0.5 12a5 5 0 0 1 10 0z"/></svg>Pro</span>
    </header>
    <div class="stage-meta">
      <span class="record"><span class="record-dot"></span>Record 00:25:36</span>
      <span class="invite"><span class="invite-plus">+</span>Invite people</span>
    </div>
    <div class="video" role="img" aria-label="Live stream photo of a couple in dark evening wear, woman in a black lace dress"></div>
    <div class="stage-foot-line"></div>
  </main>

  <section class="controls">
    <div class="volume">
      <svg viewBox="0 0 20 18"><path d="M2 6h4l5-4v14l-5-4H2z"/><path d="M14 5a5 5 0 0 1 0 8M16.5 3a8 8 0 0 1 0 12" stroke="#7b2872" stroke-width="1.6" fill="none"/></svg>
      <div class="volume-track"></div>
    </div>
    <div class="ctrl" style="left:162px"><div class="ctrl-btn"><svg viewBox="0 0 22 22" fill="none" stroke="#a8a5ae" stroke-width="1.5"><rect x="8" y="2" width="6" height="11" rx="3"/><path d="M5 10a6 6 0 0 0 12 0M11 16v4M4 19L18 3"/></svg></div>Mic</div>
    <div class="ctrl" style="left:225px"><div class="ctrl-btn"><svg viewBox="0 0 22 22" fill="#a8a5ae"><rect x="2" y="6" width="13" height="10" rx="2"/><path d="M16 10l5-3v8l-5-3z"/></svg></div>Cam</div>
    <div class="ctrl" style="left:288px"><div class="ctrl-btn"><svg viewBox="0 0 22 22" fill="#a8a5ae"><rect x="4" y="4" width="6" height="6" rx="1"/><rect x="12" y="4" width="6" height="6" rx="1"/><rect x="4" y="12" width="6" height="6" rx="1"/><rect x="12" y="12" width="6" height="6" rx="1"/></svg></div>Display</div>
    <div class="ctrl" style="left:351px"><div class="ctrl-btn is-active"><svg viewBox="0 0 24 24"><circle cx="12" cy="12" r="9" fill="none" stroke="#fff" stroke-width="2"/><circle cx="12" cy="12" r="5" fill="#fff"/></svg></div>Rec</div>
    <div class="ctrl" style="left:414px"><div class="ctrl-btn"><svg viewBox="0 0 22 22" fill="none" stroke="#7b2872" stroke-width="1.8"><path d="M4 8V4h4M14 4h4v4M18 14v4h-4M8 18H4v-4"/></svg></div>Screen</div>
    <div class="ctrl" style="left:556px"><div class="ctrl-btn"><svg viewBox="0 0 22 22" fill="#a8a5ae"><path d="M5 3h8v16H5z"/><path d="M15 11h5M18 8l3 3-3 3" stroke="#a8a5ae" stroke-width="1.6" fill="none"/></svg></div>Mic</div>
  </section>

  <aside class="panel">
    <div class="tabs">
      <div class="tab is-active">Chat</div>
      <div class="tab">Attendee</div>
    </div>
    <div class="poll">
      <p class="poll-q"><span>Which platform will be the leader</span><span>in your 2022 SMM strategy?</span></p>
      <div class="poll-list">
        <div><div class="poll-bar"><span style="width:33%"></span></div><div class="poll-label">33% Friendloop</div></div>
        <div><div class="poll-bar"><span style="width:58%"></span></div><div class="poll-label">52% Photoburst</div></div>
        <div><div class="poll-bar"><span style="width:58%"></span></div><div class="poll-label">15% Chirpline</div></div>
      </div>
    </div>
    <div class="divider">Message</div>
    <div class="msg" style="top:418px">
      <div class="avatar devi" role="img" aria-label="Profile photo of Devi"></div>
      <span class="msg-name">Devi</span>
      <div class="bubble">Hi guys, can you hear me?</div>
    </div>
    <div class="msg" style="top:510px">
      <div class="avatar octavia" role="img" aria-label="Profile photo of Octavia"></div>
      <span class="msg-name">Octavia</span>
      <div class="bubble">Yuhuu,we can jes</div>
    </div>
    <span class="you-name">You</span>
    <div class="bubble-you">Yup,we can hear you</div>
  </aside>

</div>
</body>
</html>
```